Website redesign for AI startup

Overview
We are looking to have our website https://www.hellomarlo.ai/ redesigned to look much more sophisticated and modern. We would like the brand colors to be different and less or no use of the Marlo bird character. We have included some example sites below for designs that we like. Please do not to use the same purple or purple at all on the site as we would like different brand colors and 'too much purple' has been the main comment.

Example sites that we like:
https://www.quorvant.com/
https://pagemorrow.com/
https://www.steadycloudly.com/

Requirements
Redesign the following pages from our website, modeling an example site that we like:
-Home page: https://hellomarlo.ai
-See an example: https://www.hellomarlo.ai/example-page
-Pricing: https://www.hellomarlo.ai/pricing
-Product: https://www.hellomarlo.ai/how-it-works
-Portal home: https://www.hellomarlo.ai/overview (you will need to create an account to view this; the account is free)
New design should be sleek, professional, and modern
The pages should contain the same content that it currently does.
Images on the pages should change to match the new designs and style.
Use different brand colors, these should look professional
The Marlo bird character can be used, but it’s not required. If the bird is used, it should be rarely used and not front-and-center.
Provide both desktop and mobile designs

Target Market(s)

Small business owners

Industry/Entity Type

SaaS tool

Number of Pages Required

5+ page

Requirements
Must have
• modern and sleek design, different brand colors, mobile and web designs

```html
<!DOCTYPE html>
<html lang="en">
<head>
<meta charset="utf-8">
<title>HelloMarlo – Your 24/7 AI Sales Assistant</title>
<link href="https://fonts.googleapis.com/css2?family=Nunito:wght@600;700;800;900&family=Roboto:wght@400;500;700&display=swap" rel="stylesheet">
<style>
:root{
  --blue:#1d6ff2;
  --navy:#0b1a3a;
  --ink:#111418;
  --text:#3b3f46;
  --white:#ffffff;
  --line:#dde1e7;
  --star:#f5a623;
  --black:#000000;
}
*{margin:0;padding:0;box-sizing:border-box}
html,body{width:1200px;height:4052px;overflow:hidden;background:var(--white)}
body{position:relative;font-family:"Roboto",sans-serif;color:var(--ink)}
.abs{position:absolute}

/* nav */
.nav{left:0;top:0;width:1200px;height:86px;background:var(--white)}
.brand{left:97px;top:24px;font-family:"Roboto",sans-serif;font-weight:700;font-size:28px;color:var(--ink);white-space:nowrap}
.nav-links{left:0;top:31px;font-size:15px;color:var(--ink)}
.nav-links span{position:absolute;white-space:nowrap}
.login{left:940px;top:20px;width:161px;height:46px;border-radius:23px;background:var(--blue);color:var(--white);font-family:"Nunito",sans-serif;font-weight:800;font-size:15px;display:flex;align-items:center;justify-content:center}

/* hero */
.hero{left:0;top:86px;width:1200px;height:600px;background:linear-gradient(120deg,#1a6cf0 0%,#2177f7 60%,#1c6ef2 100%)}
.hero-title{left:97px;top:228px;font-family:"Nunito",sans-serif;font-weight:900;font-size:56px;color:var(--white)}
.hero-sub{left:99px;top:306px;font-size:35px;line-height:52px;color:var(--white);font-weight:400}
.hero-sub b{font-weight:700}
.btn{display:flex;align-items:center;justify-content:center;border-radius:24px;font-family:"Nunito",sans-serif;font-weight:800;font-size:15px}
.btn-solid{left:97px;top:486px;width:161px;height:47px;background:var(--white);color:var(--blue)}
.btn-ghost{left:270px;top:486px;width:162px;height:47px;border:2px solid var(--white);color:var(--white)}
.hero-photo{left:632px;top:190px;width:469px;height:392px;border-radius:16px;background:linear-gradient(135deg,#dfe6ee,#a9b8c9 60%,#7e93ab)}

/* feature cards */
.card{border:1px solid var(--line);background:var(--white);text-align:center}
.card.raised{box-shadow:0 4px 14px rgba(0,0,0,.14)}
.card-photo{position:absolute;left:18px;top:18px;width:282px;height:196px}
.card-title{position:absolute;left:0;width:100%;font-family:"Nunito",sans-serif;font-weight:700;font-size:19px;line-height:30px;color:var(--ink)}
.card-body{position:absolute;left:22px;right:22px;font-family:"Nunito",sans-serif;font-size:14.5px;line-height:29px;color:var(--text)}
.card-link{position:absolute;left:0;width:100%;font-family:"Nunito",sans-serif;font-weight:700;font-size:15px;color:var(--ink)}

/* testimonials */
.testimonials{left:0;top:1322px;width:1200px;height:603px;background:radial-gradient(ellipse at 60% 30%,#12295a 0%,#0b1a3a 55%,#081430 100%)}
.t-title{left:0;top:1404px;width:1200px;text-align:center;font-family:"Nunito",sans-serif;font-weight:800;font-size:32px;color:var(--white)}
.quote{top:1538px;width:310px;height:190px;background:var(--white);border-radius:8px;text-align:center;padding:68px 22px 0;font-family:"Nunito",sans-serif;font-size:13px;line-height:26px;color:var(--text)}
.quote::after{content:"";position:absolute;left:147px;bottom:-8px;width:16px;height:16px;background:var(--white);transform:rotate(45deg)}
.avatar{width:92px;height:92px;border-radius:50%;border:3px solid var(--white);background:linear-gradient(160deg,#c9ced6,#7b8595)}
.t-name{top:1756px;width:310px;text-align:center;font-family:"Nunito",sans-serif;font-size:15px;color:var(--white)}
.stars{top:1794px;width:310px;text-align:center;color:var(--star);font-size:14px;letter-spacing:1px}
.arrow{top:1635px}

/* feature rows */
.row-photo{width:459px;height:342px;border-radius:24px;box-shadow:0 4px 10px rgba(0,0,0,.18)}
.row-title{font-family:"Nunito",sans-serif;font-weight:800;font-size:33px;line-height:41px;color:var(--ink)}
.row-body{font-size:19px;line-height:34px;color:var(--ink);width:365px}

/* cta */
.cta{left:0;top:3254px;width:1200px;height:313px;background:linear-gradient(120deg,#1a6cf0,#1f74f5 60%,#1867ea)}
.cta-kicker{left:0;top:3322px;width:1200px;text-align:center;font-size:25px;color:var(--white)}
.cta-title{left:0;top:3358px;width:1200px;text-align:center;font-size:52px;font-weight:500;color:var(--white)}
.cta-btn{left:519px;top:3449px;width:162px;height:47px;border:2px solid var(--white);color:var(--white)}

/* footer */
.footer{left:0;top:3567px;width:1200px;height:485px;background:var(--black)}
.f-brand{left:0;top:3650px;width:1200px;text-align:center;font-family:"Roboto",sans-serif;font-weight:700;font-size:46px;color:var(--white)}
.f-row{left:0;width:1200px;text-align:center;font-size:17px;color:var(--white)}
.f-row span{margin:0 20px}
.f-row.small span{margin:0 10px}
.social{top:3939px;width:24px;height:24px;border-radius:50%;background:var(--blue)}
</style>
</head>
<body>

<header class="abs nav">
  <div class="abs brand">HelloMarlo</div>
  <nav class="abs nav-links">
    <span style="left:432px">Home</span>
    <span style="left:506px">Product</span>
    <span style="left:594px">Support Pricing</span>
    <span style="left:734px">FAQ</span>
    <span style="left:796px">Referral Program</span>
  </nav>
  <div class="abs login">Login / Register</div>
</header>

<section class="abs hero" aria-label="Welcome"></section>
<h1 class="abs hero-title">Welcome!</h1>
<p class="abs hero-sub">Save time and get more<br>customers with helloMarlo:<br>Your 24/7 AI <b>Sales Assistant</b></p>
<div class="abs btn btn-solid">See an Example!</div>
<div class="abs btn btn-ghost">Create your Marlo</div>
<div class="abs hero-photo" role="img" aria-label="Photo of a smiling support agent wearing a headset at an office desk"></div>

<div class="abs card" style="left:97px;top:782px;width:318px;height:430px">
  <div class="card-photo" role="img" aria-label="Hands typing on a laptop with glowing teal interface icons" style="background:linear-gradient(135deg,#0f6a64,#35b3a4 55%,#0d4d4a)"></div>
  <div class="card-title" style="top:238px">24/7 Customer Engagement</div>
  <div class="card-body" style="top:277px">Marlo interacts with your leads across email, chatbot, phone, and text around the clock.</div>
  <div class="card-link" style="top:374px">See an example here.</div>
</div>
<div class="abs card raised" style="left:440px;top:782px;width:318px;height:430px">
  <div class="card-photo" role="img" aria-label="Presenter speaking to a seated business audience in a bright room" style="background:linear-gradient(135deg,#8a96a6,#c9ced3 50%,#5d4b45)"></div>
  <div class="card-title" style="top:233px">Lead Qualification &amp;<br>Prioritization</div>
  <div class="card-body" style="top:302px">Marlo captures, engages, and qualifies leads, helping you focus on the most promising opportunities.</div>
</div>
<div class="abs card" style="left:783px;top:782px;width:318px;height:430px">
  <div class="card-photo" role="img" aria-label="Person writing in a notebook at a desk beside a laptop" style="background:linear-gradient(135deg,#3b3a3a,#c9b59c 55%,#e9dfd2)"></div>
  <div class="card-title" style="top:238px">Automated Scheduling</div>
  <div class="card-body" style="top:277px">Marlo books meetings with qualified leads directly on your calendar, streamlining your sales process.</div>
  <div class="card-link" style="top:374px">See an example here.</div>
</div>

<section class="abs testimonials" aria-label="Client Testimonials"></section>
<h2 class="abs t-title">Client Testimonials</h2>

<svg class="abs arrow" style="left:40px" width="22" height="32" viewBox="0 0 22 32" aria-hidden="true"><path d="M17 3 L5 16 L17 29" fill="none" stroke="#fff" stroke-width="2.5"/></svg>
<svg class="abs arrow" style="left:1138px" width="22" height="32" viewBox="0 0 22 32" aria-hidden="true"><path d="M5 3 L17 16 L5 29" fill="none" stroke="#fff" stroke-width="2.5"/></svg>

<div class="abs quote" style="left:99px">It took me less than 5 minutes to get my Marlo AI Assistant up and running, and with the 24/7 customer support, I'm already my weekends and week nights back."</div>
<div class="abs avatar" style="left:208px;top:1492px" role="img" aria-label="Portrait of the client"></div>
<div class="abs t-name" style="left:99px">Renata Holloway, Real Estate Broker</div>
<div class="abs stars" style="left:99px">★★★★★</div>

<div class="abs quote" style="left:445px">It's amazing to see what Marlo can do. It's such a timesaver and painless way to helloMarlo Sales Assistant qualify prospective</div>
<div class="abs avatar" style="left:554px;top:1492px" role="img" aria-label="Portrait of the client"></div>
<div class="abs t-name" style="left:445px">Marisa Quendel, Certified Financial Planner</div>
<div class="abs stars" style="left:445px">★★★★★</div>

<div class="abs quote" style="left:791px">"There's no other AI assistant like helloMarlo on the market. Best kept secret for sure."</div>
<div class="abs avatar" style="left:900px;top:1492px" role="img" aria-label="Portrait of the client"></div>
<div class="abs t-name" style="left:791px">Tomas Brevick, Landscaper</div>
<div class="abs stars" style="left:791px">★★★★★</div>

<div class="abs row-photo" style="left:96px;top:2016px;background:linear-gradient(120deg,#b9c7d6,#5d7590 50%,#1e2d40)" role="img" aria-label="Humanoid robot working beside a laptop with floating data panels"></div>
<h3 class="abs row-title" style="left:678px;top:2074px">Rapid and Effective<br>AI Training</h3>
<p class="abs row-body" style="left:678px;top:2182px">Marlo analyzes your website, allowing Marlo to provide accurate and up-to-date information to your leads.</p>

<h3 class="abs row-title" style="left:129px;top:2470px">Customize Your Assistant</h3>
<p class="abs row-body" style="left:129px;top:2534px">Change your phone number, email, how Marlo engages with your leads, and much more, turning every interaction into an opportunity.</p>
<div class="abs row-photo" style="left:642px;top:2406px;background:linear-gradient(120deg,#e9e6e1,#d9b062 45%,#9aa7b6)" role="img" aria-label="Two colleagues working together at a laptop in a bright office"></div>

<div class="abs row-photo" style="left:96px;top:2804px;background:linear-gradient(180deg,#2f8f86,#2a7f78 60%,#1e3a4a)" role="img" aria-label="Illustration of three people at computers under a cloud of tool icons"></div>
<h3 class="abs row-title" style="left:678px;top:2866px">Seamless Tool Integration</h3>
<p class="abs row-body" style="left:678px;top:2933px">helloMarlo's streamlined tool integrations effortlessly sync with your existing business tools and platforms, ensuring a smooth and seamless setup.</p>

<section class="abs cta" aria-label="Set up"></section>
<div class="abs cta-kicker">SET UP</div>
<div class="abs cta-title">your own Marlo</div>
<div class="abs btn cta-btn">Create your Marlo</div>

<footer class="abs footer"></footer>
<div class="abs f-brand">HelloMarlo</div>
<div class="abs f-row" style="top:3764px"><span>Home</span><span>Product</span><span>Support</span><span>Pricing</span><span>FAQ</span><span>Referral Program</span></div>
<div class="abs f-row small" style="top:3823px"><span>Have feedback?</span><span>Let us know!</span><span>Privacy Policy</span><span>Terms of Use</span></div>
<div class="abs f-row" style="top:3879px">© 2024 HelloMarlo.ai. All rights reserved.</div>
<div class="abs social" style="left:531px" aria-label="Social link"></div>
<div class="abs social" style="left:569px" aria-label="Social link"></div>
<div class="abs social" style="left:607px" aria-label="Social link"></div>
<div class="abs social" style="left:645px" aria-label="Social link"></div>

</body>
</html>
```